Business card design for Virtual Assistance company

I need a business card designed for my virtual assistance company. We are a small company who services primarily C-level executive clients. The card needs to be double sided with the following contact information on the back:
Melissa Thornbury
Owner/CEO
info@rkpadvisory.net
www.rkpadvisory.net
555.302.9817

The front side should just have the company name incorporated: "RKP Advisory" and "virtual assistance"

The card should be simplistic, but eye catching and should speak to high level executives. Our primary focus areas consist of executive assistance and government contracting.

Target Market(s)

CEOs and executives

Contact Information for Business Card

see project description. phone, email, website.

Colors

Designer to choose only greyscale colors for use in the design.

```html
<!DOCTYPE html>
<html lang="en">
<head>
<meta charset="utf-8">
<title>RKP Advisory – Business Card</title>
<link rel="stylesheet" href="https://fonts.googleapis.com/css2?family=Cormorant+Garamond:wght@500&family=Crimson+Pro:wght@700&family=Montserrat:wght@400&display=swap">
<style>
  :root {
    --backdrop: #e9e9e9;
    --card-white: #ffffff;
    --ink: #111111;
    --band: #1f1f1f;
    --rule: #2a2a2a;
    --back-light: #3b3b3b;
    --back-dark: #0f0f0f;
    --paper-text: #ffffff;
  }
  * { margin: 0; padding: 0; box-sizing: border-box; }
  html, body {
    width: 1200px; height: 1108px; overflow: hidden;
    background: var(--backdrop);
  }
  .canvas { position: relative; width: 1200px; height: 1108px; }

  .card { position: absolute; border-radius: 22px; overflow: hidden; }

  /* Contact side */
  .card--contact {
    left: 222px; top: 52px; width: 786px; height: 479px;
    background: var(--card-white);
  }
  .wordmark {
    position: absolute; right: 426px; top: 228px;
    font-family: "Cormorant Garamond", serif; font-weight: 500;
    font-size: 42px; color: var(--ink); white-space: nowrap; letter-spacing: -0.3px;
  }
  .divider {
    position: absolute; left: 389px; top: 177px; width: 2px; height: 161px;
    background: var(--rule);
  }
  .holder-name {
    position: absolute; left: 413px; top: 174px;
    font-family: "Crimson Pro", serif; font-weight: 700;
    font-size: 30px; color: var(--ink); white-space: nowrap;
  }
  .holder-title {
    position: absolute; left: 413px; top: 212px;
    font-family: "Montserrat", sans-serif; font-size: 17px; color: var(--ink);
  }
  .contact-list { position: absolute; left: 414px; top: 253px; list-style: none; }
  .contact-item {
    display: flex; align-items: center; height: 31px;
    font-family: "Montserrat", sans-serif; font-size: 17px; color: var(--ink);
  }
  .contact-icon { width: 18px; height: 18px; margin-right: 9px; flex: none; }
  .tagline-band {
    position: absolute; left: 0; top: 389px; width: 100%; height: 58px;
    background: var(--band); display: flex; align-items: center; justify-content: center;
    font-family: "Cormorant Garamond", serif; font-weight: 500;
    font-size: 18px; color: var(--paper-text); letter-spacing: 0.2px;
  }

  /* Brand side */
  .card--brand {
    left: 220px; top: 578px; width: 788px; height: 462px;
    background: var(--back-dark);
  }
  .brand-texture {
    position: absolute; inset: 0;
    background: linear-gradient(100deg, var(--back-light) 0%, #262626 35%, var(--back-dark) 60%, #141414 100%);
  }
  .brand-name {
    position: absolute; right: 88px; top: 305px;
    font-family: "Cormorant Garamond", serif; font-weight: 500;
    font-size: 40px; color: var(--paper-text); white-space: nowrap;
  }
</style>
</head>
<body>
<main class="canvas">

  <section class="card card--contact" aria-label="Card contact side">
    <div class="wordmark">RKP Advisory</div>
    <div class="divider"></div>
    <h1 class="holder-name">Melissa Thornbury</h1>
    <p class="holder-title">Owner/CEO</p>
    <ul class="contact-list">
      <li class="contact-item">
        <svg class="contact-icon" viewBox="0 0 24 24" aria-hidden="true"><path fill="#111" d="M6.6 10.8c1.4 2.8 3.8 5.1 6.6 6.6l2.2-2.2c.3-.3.7-.4 1-.2 1.1.4 2.3.6 3.6.6.6 0 1 .4 1 1V20c0 .6-.4 1-1 1C10.6 21 3 13.4 3 4c0-.6.4-1 1-1h3.5c.6 0 1 .4 1 1 0 1.3.2 2.5.6 3.6.1.3 0 .7-.2 1z"/><path fill="none" stroke="#111" stroke-width="1.8" stroke-linecap="round" d="M14.5 3.5a6 6 0 0 1 6 6M14.5 7a2.6 2.6 0 0 1 2.6 2.6"/></svg>
        555.302.9817
      </li>
      <li class="contact-item">
        <svg class="contact-icon" viewBox="0 0 24 24" aria-hidden="true"><rect x="3" y="5" width="18" height="14" rx="1.5" fill="#111"/><path d="M3.5 6l8.5 6.5L20.5 6" fill="none" stroke="#fff" stroke-width="1.6"/></svg>
        info@rkpadvisory.net
      </li>
      <li class="contact-item">
        <svg class="contact-icon" viewBox="0 0 24 24" aria-hidden="true"><circle cx="12" cy="12" r="9.5" fill="#111"/><path d="M3 12h18M12 2.5c3 3 3 16 0 19M12 2.5c-3 3-3 16 0 19" fill="none" stroke="#fff" stroke-width="1.3"/></svg>
        www.rkpadvisory.net
      </li>
    </ul>
    <div class="tagline-band">VIRTUAL ASSISTANCE</div>
  </section>

  <section class="card card--brand" aria-label="Card brand side">
    <div class="brand-texture" role="img" aria-label="Tonal repeating brand pattern in dark and mid greys"></div>
    <div class="brand-name">RKP Advisory</div>
  </section>

</main>
</body>
</html>
```